Maple Gable Business Card

Colors can be blue, grey and white as you see in the attached logo. Needs to have a spot for name, title, phone, email, address, and website. There also needs to be a spot for an agent's picture.

Contact Information for Business Card

See project description.

Colors

Designer to choose colors to be used in the design.

```html
<!DOCTYPE html>
<html lang="en">
<head>
<meta charset="utf-8">
<title>Maple Gable Business Card</title>
<link href="https://fonts.googleapis.com/css2?family=Montserrat:wght@400;500;600;700&display=swap" rel="stylesheet">
<style>
  :root {
    --blue: #2a78bd;
    --blue-deep: #2266a5;
    --blue-emboss: #2a70b0;
    --grey: #4a4b4f;
    --grey-soft: #6b6c70;
    --photo-light: #dfe6ee;
    --photo-dark: #b9c6d4;
    --white: #ffffff;
    --stage: #e6e8eb;
  }
  * { margin: 0; padding: 0; box-sizing: border-box; }
  html, body { width: 1200px; height: 852px; overflow: hidden; }
  body {
    background: var(--stage);
    font-family: "Montserrat", sans-serif;
    position: relative;
  }
  .card {
    position: absolute;
    width: 540px;
    height: 309px;
    border-radius: 16px;
    overflow: hidden;
    box-shadow: 0 6px 18px rgba(0,0,0,0.12);
  }
  .card--back { left: 40px; top: 272px; background: var(--blue); }
  .card--front { left: 620px; top: 272px; background: var(--white); }

  .back-brand {
    position: absolute; inset: 0;
    display: flex; flex-direction: column; align-items: center; justify-content: center;
    color: var(--blue-emboss);
  }
  .back-brand__mark { width: 34px; height: 34px; background: var(--blue-emboss); margin-bottom: 14px; }
  .back-brand__name { font-weight: 700; font-size: 38px; letter-spacing: 1px; text-transform: uppercase; }
  .back-brand__tag { font-weight: 700; font-size: 15px; letter-spacing: 5px; text-transform: uppercase; margin-top: 4px; }

  .brand { position: absolute; left: 28px; top: 40px; color: var(--blue); }
  .brand__row { display: flex; align-items: center; gap: 8px; }
  .brand__mark { width: 18px; height: 18px; background: var(--blue); }
  .brand__name { font-weight: 700; font-size: 22px; text-transform: uppercase; letter-spacing: 0.5px; }
  .brand__tag { font-weight: 700; font-size: 9px; letter-spacing: 4px; text-transform: uppercase; margin: 4px 0 0 26px; }

  .agent-photo {
    position: absolute; left: 28px; top: 90px;
    width: 78px; height: 78px; border-radius: 50%;
    background: linear-gradient(160deg, var(--photo-light), var(--photo-dark));
    border: 3px solid var(--blue);
  }

  .agent { position: absolute; right: 28px; top: 44px; text-align: right; }
  .agent__name { color: var(--blue); font-weight: 700; font-size: 21px; text-transform: uppercase; letter-spacing: 0.5px; }
  .agent__title { color: var(--grey); font-size: 12px; margin-top: 3px; }
  .accent-tab { position: absolute; right: 0; top: 44px; width: 10px; height: 34px; background: var(--blue); }
  .rule { position: absolute; height: 1px; background: var(--blue); }
  .rule--name { right: 28px; top: 98px; width: 240px; }
  .rule--contact { left: 28px; top: 180px; width: 240px; }

  .address { position: absolute; right: 28px; top: 112px; text-align: right; color: var(--grey); font-size: 13px; line-height: 1.55; }

  .contact { position: absolute; left: 28px; top: 188px; list-style: none; color: var(--grey); font-size: 13px; }
  .contact li { display: flex; align-items: center; gap: 8px; line-height: 1.55; }
  .contact svg { width: 11px; height: 11px; flex: none; }

  .wave { position: absolute; left: 0; bottom: 0; width: 540px; height: 309px; }
</style>
</head>
<body>

<section class="card card--back" aria-label="Card back">
  <div class="back-brand">
    <div class="back-brand__mark"></div>
    <div class="back-brand__name">Maple Gable</div>
    <div class="back-brand__tag">Real Estate</div>
  </div>
</section>

<section class="card card--front" aria-label="Card front">
  <div class="brand">
    <div class="brand__row">
      <div class="brand__mark"></div>
      <div class="brand__name">Maple Gable</div>
    </div>
    <div class="brand__tag">Real Estate</div>
  </div>

  <div class="agent-photo" role="img" aria-label="Agent portrait photo"></div>

  <div class="accent-tab"></div>
  <div class="agent">
    <div class="agent__name">Daniel Hartley</div>
    <div class="agent__title">Director</div>
  </div>
  <div class="rule rule--name"></div>

  <div class="address">48 Linden Row<br>Brookfield, MA 01506</div>

  <div class="rule rule--contact"></div>
  <ul class="contact">
    <li>
      <svg viewBox="0 0 12 12"><path d="M2.5 1 L4.5 1 L5.2 3.6 L4 4.5 C4.6 5.9 6.1 7.4 7.5 8 L8.4 6.8 L11 7.5 L11 9.5 C11 10.4 10.3 11 9.5 11 C5 10.7 1.3 7 1 2.5 C1 1.7 1.6 1 2.5 1 Z" fill="var(--blue)"/></svg>
      555 014-2290
    </li>
    <li>
      <svg viewBox="0 0 12 12"><rect x="1" y="2.5" width="10" height="7" fill="none" stroke="var(--blue)" stroke-width="1.3"/><path d="M1 2.5 L6 6.5 L11 2.5" fill="none" stroke="var(--blue)" stroke-width="1.3"/></svg>
      info@maplegable.com
    </li>
    <li>
      <svg viewBox="0 0 12 12"><circle cx="6" cy="6" r="5" fill="none" stroke="var(--blue)" stroke-width="1.2"/><ellipse cx="6" cy="6" rx="2.2" ry="5" fill="none" stroke="var(--blue)" stroke-width="1"/><path d="M1 6 H11" stroke="var(--blue)" stroke-width="1"/></svg>
      www.maplegable.com
    </li>
  </ul>

  <svg class="wave" viewBox="0 0 540 309" aria-hidden="true">
    <path d="M0,296 C120,296 230,284 330,248 C420,216 480,200 540,194 L540,309 L0,309 Z" fill="var(--blue)"/>
    <path d="M0,290 C120,290 230,276 330,240 C420,208 480,192 540,186" fill="none" stroke="var(--grey)" stroke-width="5"/>
    <path d="M0,296 C120,296 230,284 330,248 C420,216 480,200 540,194" fill="none" stroke="var(--white)" stroke-width="3"/>
  </svg>
</section>

</body>
</html>
```